Business Card for: Bramwell Financial Advisory Services Inc.

provide strategic financial advisory services to companies in the areas of corporate finance, mergers and acquisitions, executive coaching and strategic planning

Target Market(s)

Companies, banks, accountants, lawyers

Industry/Entity Type

High end business consulting in corporate finance, mergers and acquisitions, consulting

Contact Information for Business Card

Name of company, Name: xxxxxx xxxxxx , CEO, - phone number: 1-xxx-xxx-xxxx, - email address,

Requirements
Must have
• Must be professional and simple.
Nice to have
• simple, straight graphics, must give the impression that we are trustworthy, professional, competent
Should not have
• loud colors, loud design features

```html
<!DOCTYPE html>
<html lang="en">
<head>
<meta charset="utf-8">
<title>Bramwell Financial Advisory Services Inc. — Business Card</title>
<link href="https://fonts.googleapis.com/css2?family=Montserrat:wght@400;500;600&display=swap" rel="stylesheet">
<style>
  :root {
    --backdrop: #282828;
    --card: #000000;
    --gold: #c9a04a;
    --gold-light: #e6cf7e;
    --gold-deep: #a87a2c;
  }
  * { margin: 0; padding: 0; box-sizing: border-box; }
  html, body {
    width: 1200px; height: 1015px; overflow: hidden;
    background: var(--backdrop);
    font-family: "Montserrat", sans-serif;
  }
  .stage {
    width: 1200px; height: 1015px;
    display: flex; flex-direction: column; align-items: center; justify-content: center;
    gap: 56px;
  }
  .card {
    width: 620px; height: 354px;
    background: var(--card);
    box-shadow: 0 14px 30px rgba(0,0,0,.55);
    position: relative;
    color: var(--gold);
  }
  /* Front */
  .card-front {
    display: flex; flex-direction: column; align-items: center; justify-content: center;
  }
  .brand-mark {
    display: flex; align-items: center; gap: 16px;
  }
  .brand-dot {
    width: 34px; height: 34px; border-radius: 50%;
    background: var(--gold);
  }
  .brand-name {
    font-size: 54px; font-weight: 500; letter-spacing: 1px;
    color: var(--gold);
    line-height: 1;
  }
  .brand-tagline {
    margin-top: 14px;
    font-size: 17px; font-weight: 500; letter-spacing: 1.5px;
    color: var(--gold-light);
  }
  /* Back */
  .card-back {
    display: flex; align-items: center; justify-content: center;
    padding-left: 40px;
  }
  .person { text-align: right; }
  .person-name {
    font-size: 29px; font-weight: 500; color: var(--gold);
    line-height: 1.1;
  }
  .person-name strong { font-weight: 600; color: var(--gold-light); }
  .person-role {
    font-size: 15px; font-weight: 500; letter-spacing: .5px;
    color: var(--gold-light);
    margin-top: 2px;
  }
  .divider {
    width: 1.5px; height: 78px;
    background: var(--gold-deep);
    margin: 0 22px;
  }
  .contact-list { list-style: none; }
  .contact-item {
    display: flex; align-items: center; gap: 8px;
    font-size: 14px; font-weight: 500; letter-spacing: .3px;
    color: var(--gold-light);
    line-height: 24px;
  }
  .contact-icon { width: 14px; height: 14px; fill: none; stroke: var(--gold); stroke-width: 1.6; }
</style>
</head>
<body>
<main class="stage">
  <section class="card card-front">
    <div class="brand-mark">
      <span class="brand-dot"></span>
      <span class="brand-name">Bramwell</span>
    </div>
    <p class="brand-tagline">Financial Advisory Services Inc.</p>
  </section>

  <section class="card card-back">
    <div class="person">
      <p class="person-name">Marcus <strong>Ellery</strong></p>
      <p class="person-role">Managing Director</p>
    </div>
    <span class="divider"></span>
    <ul class="contact-list">
      <li class="contact-item">
        <svg class="contact-icon" viewBox="0 0 16 16"><path d="M3 2h3l1 4-2 1a9 9 0 0 0 4 4l1-2 4 1v3a1 1 0 0 1-1 1A13 13 0 0 1 2 3a1 1 0 0 1 1-1z"/></svg>
        044-555 010 200
      </li>
      <li class="contact-item">
        <svg class="contact-icon" viewBox="0 0 16 16"><rect x="1.5" y="3.5" width="13" height="9"/><path d="M1.5 3.5 8 9l6.5-5.5"/></svg>
        info@bramwelladvisory.com
      </li>
      <li class="contact-item">
        <svg class="contact-icon" viewBox="0 0 16 16"><circle cx="8" cy="8" r="6.5"/><path d="M1.5 8h13M8 1.5c3 3.5 3 9.5 0 13M8 1.5c-3 3.5-3 9.5 0 13"/></svg>
        www.bramwelladvisory.com
      </li>
    </ul>
  </section>
</main>
</body>
</html>
```